Förderverein einer Kirchengemeinde sucht Flyer-Design
Zielgruppe
Wir sind ein Förderverein einer Kirchengemeinde, der sich für die kirchenmusikalische Arbeit einsetzt.
Wir wünschen uns ein niveauvolles und zeitgemäßes/modernes Flyerdesign, das die etablierten Konzertbesucher anspricht, aber vor allem auch Menschen erreicht und überzeugt, die (noch) nichts mit Kirche zu tun haben.
Das Alter der (Haupt-) Zielgruppe (Männer und Frauen) erstreckt sich von 45 bis 70 Jahren.
Aufgabenstellung
Bei der Wahl des Formates würden wir (aus der Sicht von Laien) ein zweimal gefaltetes DIN A4 quer Format nehmen. Aber wir lassen uns gerne überraschen und sind grundsätzlich für andere Lösungen offen.
Bitte den Abschnitt für Adress- und sonstige Dateneintragungen samt Kontodaten so gestalten und platzieren, dass man ihn leicht abtrennen und verschicken kann.
Der Flyer soll Kirchenmusik als lebendig und attraktiv darstellen und neue (jüngere) Mitglieder für den Freundeskreis werben.
Lassen Sie die Bilder sprechen!!

```html
<!DOCTYPE html>
<html lang="de">
<head>
<meta charset="utf-8">
<title>Förderkreis Kirchenklang – Beitrittserklärung</title>
<link rel="stylesheet" href="https://fonts.googleapis.com/css2?family=Mulish:ital,wght@0,400;0,600;0,700;0,800;1,400&display=swap">
<style>
:root{
  --red:#c0161b;
  --ink:#4a4a4a;
  --rule:#cfcfcf;
  --band:#dadada;
  --white:#ffffff;
  --paper:#ffffff;
}
*{margin:0;padding:0;box-sizing:border-box}
html,body{width:1200px;height:846px;overflow:hidden;background:var(--paper)}
body{font-family:"Mulish",sans-serif;color:var(--ink);position:relative}
.abs{position:absolute}
.form-title{left:36px;top:22px;font-size:27px;font-weight:700;color:var(--red);letter-spacing:.2px}
.field-grid{left:36px;top:69px;width:656px;height:232px;border:1.5px solid var(--rule)}
.field{position:absolute;font-size:15px;padding-left:7px;padding-top:8px;white-space:nowrap}
.hline{position:absolute;height:1.5px;background:var(--rule)}
.vline{position:absolute;width:1.5px;background:var(--rule)}
.band{position:absolute;background:var(--band);font-weight:700;color:#555;font-size:19px;padding-left:8px}
.checks{font-size:16px}
.check{position:absolute;display:flex;align-items:center;white-space:nowrap}
.box{width:14px;height:14px;border:1.5px solid #8a8a8a;margin-right:5px;flex:none}
.note{font-style:italic}
.sepa{left:36px;top:484px;width:656px;height:250px;border:1.5px solid var(--rule)}
.account{font-size:14px;line-height:22px}
.account-label{left:36px;top:753px;font-size:19px;font-weight:600;color:#555}
.cut-line{left:718px;top:0;width:0;height:846px;border-left:2px dashed #555}
.cut-hint{left:703px;top:830px;font-size:9px;transform:rotate(-90deg);transform-origin:left top;color:#666;white-space:nowrap}
.photo{left:726px;top:0;width:474px;height:423px;background:linear-gradient(180deg,#d9d4c7 0%,#cbb98a 18%,#b9a6a0 40%,#a86a64 60%,#c9c4bc 82%,#e4e0da 100%)}
.panel{left:726px;top:423px;width:474px;height:423px;background:var(--red)}
.brand{left:726px;top:452px;width:474px;display:flex;align-items:center;justify-content:center;gap:12px;font-size:19px;font-weight:800;letter-spacing:.4px;color:var(--white)}
.brand-dot{width:20px;height:20px;border-radius:50%;background:var(--white)}
.intro{left:779px;top:513px;font-size:18px;line-height:22.5px;letter-spacing:.2px;color:var(--white)}
.address{left:829px;top:617px;font-size:20px;font-weight:700;line-height:24px;letter-spacing:.3px;color:var(--white)}
.more{left:779px;top:762px;font-size:18px;line-height:26px;color:var(--white)}
.more b{font-size:20px}
</style>
</head>
<body>

<h1 class="abs form-title">Beitrittserklärung</h1>

<section class="abs field-grid">
  <div class="field" style="left:0;top:2px">Name, Vorname</div>
  <div class="hline" style="left:0;top:33px;width:100%"></div>
  <div class="field" style="left:0;top:35px">Institution/Firma</div>
  <div class="hline" style="left:0;top:67px;width:100%"></div>
  <div class="field" style="left:0;top:69px">Straße, Hausnr., PLZ, Ort</div>
  <div class="hline" style="left:7px;top:99px;width:634px"></div>
  <div class="hline" style="left:0;top:133px;width:100%"></div>
  <div class="field" style="left:0;top:135px">Telefon/Mobil</div>
  <div class="field" style="left:326px;top:135px">Geburtsdatum</div>
  <div class="hline" style="left:0;top:169px;width:100%"></div>
  <div class="field" style="left:0;top:169px">E-Mail</div>
  <div class="field" style="left:326px;top:169px">Datum, Unterschrift</div>
  <div class="hline" style="left:7px;top:220px;width:301px"></div>
  <div class="hline" style="left:334px;top:220px;width:314px"></div>
  <div class="vline" style="left:324px;top:133px;height:97px"></div>
</section>

<div class="band" style="left:36px;top:323px;width:656px;height:32px;line-height:32px">Mitgliedsbeiträge</div>

<section class="checks">
  <div class="check" style="left:43px;top:372px"><span class="box"></span>Einzelpersonen € 20,-</div>
  <div class="check" style="left:43px;top:396px"><span class="box"></span>Ehepaare/Partnerschaften € 32,-</div>
  <div class="check" style="left:43px;top:420px"><span class="box"></span>Institutionen/Firmen € 95,-</div>
  <div class="check note" style="left:61px;top:445px;font-size:14px">(jeweils Mindestbeiträge)</div>
  <div class="check" style="left:350px;top:372px"><span class="box" style="margin-right:8px"></span>Gewünschter Betrag: €</div>
  <div class="hline" style="left:543px;top:394px;width:146px"></div>
  <div class="check" style="left:350px;top:403px"><span class="box" style="margin-right:8px"></span>Einmalige Spende&nbsp;<i>(ohne Mitgliedschaft)</i></div>
  <div class="check" style="left:350px;top:434px"><span class="box" style="margin-right:8px"></span>Ich benötige eine Spendenbescheinigung</div>
</section>

<section class="abs sepa">
  <div class="band" style="left:0;top:0;width:100%;height:31px;line-height:31px;padding-left:5px">SEPA-Lastschriftmandat</div>
  <div class="field" style="left:0;top:36px">IBAN</div>
  <div class="field" style="left:391px;top:36px">BIC</div>
  <div class="vline" style="left:390px;top:31px;height:40px"></div>
  <div class="hline" style="left:0;top:71px;width:100%"></div>
  <div class="field" style="left:0;top:79px">Kreditinstitut</div>
  <div class="field" style="left:323px;top:79px">Kontoinhaber</div>
  <div class="vline" style="left:321px;top:71px;height:45px"></div>
  <div class="hline" style="left:0;top:115px;width:100%"></div>
  <div class="field" style="left:0;top:122px;line-height:18px;width:640px;white-space:normal">Hiermit ermächtige ich den Förderkreis Kirchenklang den von mir zu entrichtenden Mitgliedsbeitrag von meinem Konto einzuziehen</div>
  <div class="field" style="left:0;top:176px">Ort, Datum, Unterschrift</div>
  <div class="hline" style="left:199px;top:199px;width:440px"></div>
  <div class="hline" style="left:0;top:212px;width:100%"></div>
  <div class="field note" style="left:0;top:214px;font-size:13.5px">Der Einzug der Mitgliedsbeiträge erfolgt zu Beginn eines Kalenderjahres</div>
</section>

<div class="abs account-label">Spendenkonto:</div>
<div class="abs account" style="left:176px;top:755px">
  Talbrücker Bürgerbank<br>
  IBAN: DE00 1234 5678 9012 3456 78<br>
  BIC: TALBDE21XXX
</div>

<div class="abs cut-line"></div>
<svg class="abs" style="left:704px;top:734px" width="16" height="20" viewBox="0 0 16 20" aria-hidden="true">
  <circle cx="4" cy="4" r="2.6" fill="none" stroke="#555" stroke-width="1.2"/>
  <circle cx="12" cy="4" r="2.6" fill="none" stroke="#555" stroke-width="1.2"/>
  <line x1="5.5" y1="6" x2="11" y2="19" stroke="#555" stroke-width="1.2"/>
  <line x1="10.5" y1="6" x2="5" y2="19" stroke="#555" stroke-width="1.2"/>
</svg>
<div class="abs cut-hint">Hier abtrennen</div>

<div class="abs photo" role="img" aria-label="Foto: barocker Orgelprospekt mit silbernen Pfeifen, goldenen Schnitzereien und rot marmoriertem Gehäuse"></div>

<section class="abs panel"></section>
<div class="abs brand">
  <span class="brand-dot"></span><span>FÖRDERKREIS KIRCHENKLANG</span>
</div>
<p class="abs intro">
  Wenn Sie die Kirchenmusik an St. Aurelien<br>
  als Mitglied im <b>Förderkreis Kirchenklang</b><br>
  fördern möchten, senden Sie die ausgefüllte<br>
  Beitrittserklärung an den
</p>
<p class="abs address">
  Förderkreis Kirchenklang<br>
  Kirchengemeinde St. Aurelien<br>
  <span style="display:block;height:13px"></span>
  Lindenweg 7, 30999 Talbrück<br>
  Tel.: 01234-5678-90<br>
  marie.lenz@kmtb.de
</p>
<p class="abs more">
  Nähere Informationen finden Sie unter<br>
  <b>www.kirchenklang-talbrueck.de</b>
</p>

</body>
</html>
```